ORV Web Design Project

I'm looking for a small, friendly,functional, information based website. If you go through the attachments, you would know the nature of the business.
Updates

Hi,

I have uploaded a picture of the CEO, Mr. Delvan Kroth PLMAT member. Please feel free to use it whereever appropriate.

Thanks!

Hello, I have uploaded some references. I like the colours used on the bar and would w

Example of a we page . I like this layout for the inside pages.

I am changing the tabs on my website to:

Home
About us
Services
Contact us

The services tab will have three sub pages:

Immigration
Education
AccommodationAccommodation

Target Market(s)

Young international students willing to come to Canada to study, young international students willing to immigrate to Canada, parents of the students

Industry/Entity Type

Business

Requirements
Must have
• ORV HOME
ABOUT US
CONTACT
SERVICES
TAG LINE

The website should look n feel trendy, smart, current, factual, trustworthy etc....
Nice to have
• I am looking for a bold, attractive, eye catchy home page with less text! Something that makes a statement....
Should not have
• No Clip art, flash animation, no bells n whistles please

```html
<!DOCTYPE html>
<html lang="en">
<head>
<meta charset="utf-8">
<title>ORV – About Us</title>
<link rel="stylesheet" href="https://fonts.googleapis.com/css2?family=Jost:wght@500;600;700;800&family=Mulish:wght@400;500&display=swap">
<style>
  :root {
    --red: #ec1c24;
    --black: #050505;
    --white: #ffffff;
    --text: #111111;
    --grey-text: #9a9a9a;
    --badge-blue: #5a86c4;
  }
  * { margin: 0; padding: 0; box-sizing: border-box; }
  html, body { width: 1200px; height: 764px; overflow: hidden; background: var(--white); }
  .page { position: relative; width: 1200px; height: 764px; font-family: "Mulish", sans-serif; color: var(--text); }

  .backdrop-map {
    position: absolute; left: 270px; top: 55px; width: 760px; height: 640px;
    background: radial-gradient(ellipse at 50% 45%, rgba(236,28,36,0.28) 0%, rgba(236,28,36,0.14) 45%, rgba(236,28,36,0) 72%);
  }

  .brand { position: absolute; left: 97px; top: 88px; }
  .brand-name {
    font-family: "Jost", sans-serif; font-weight: 800; font-size: 72px; line-height: 1;
    color: var(--black); letter-spacing: -2px; display: flex; align-items: center; gap: 8px;
  }
  .brand-mark { width: 18px; height: 18px; background: var(--red); border-radius: 50%; }
  .brand-tagline { font-family: "Mulish", sans-serif; font-weight: 400; font-size: 13px; color: var(--text); margin-top: 4px; }

  .headline { position: absolute; left: 447px; top: 50px; font-family: "Jost", sans-serif; font-weight: 800; line-height: 1; }
  .headline-top { font-size: 62px; color: var(--black); letter-spacing: -2px; }
  .headline-bottom { font-size: 62px; color: var(--red); margin-left: 233px; margin-top: -6px; letter-spacing: -2.5px; }

  .main-nav { position: absolute; left: 97px; top: 200px; width: 147px; list-style: none; }
  .main-nav li { height: 29px; margin-bottom: 2.5px; background: var(--black); display: flex; align-items: center; }
  .main-nav li.is-active { background: var(--red); }
  .main-nav a {
    display: flex; align-items: center; gap: 4px; color: var(--white); text-decoration: none;
    font-family: "Jost", sans-serif; font-weight: 700; font-size: 17.5px; padding-left: 2px;
  }
  .nav-arrow { width: 15px; height: 12px; }

  .content-panel {
    position: absolute; left: 302px; top: 176px; width: 803px; height: 459px;
    background: var(--white); box-shadow: 0 6px 18px rgba(0,0,0,0.22);
    padding: 20px 32px 0 36px;
  }
  .content-panel h1 {
    font-family: "Jost", sans-serif; font-weight: 500; font-size: 38px; color: var(--red);
    line-height: 1; margin-bottom: 22px;
  }
  .content-panel p { font-size: 13.6px; line-height: 21px; margin-bottom: 10px; }
  .content-panel .highlight { color: var(--red); }
  .portrait-slot {
    float: right; width: 188px; height: 225px; margin: 2px 0 0 14px; background: var(--black);
    display: flex; align-items: center; justify-content: center; text-align: center;
    font-family: "Jost", sans-serif; font-weight: 700; font-size: 21px; line-height: 26px; color: var(--grey-text);
  }

  .member-badge { position: absolute; left: 97px; top: 660px; width: 78px; height: 78px; border-radius: 50%; background: var(--badge-blue); opacity: 0.85; }
  .copyright { position: absolute; left: 0; width: 1200px; top: 701px; text-align: center; font-size: 11px; color: var(--text); }
  .social { position: absolute; left: 977px; top: 698px; display: flex; gap: 6px; list-style: none; }
  .social li { width: 26px; height: 26px; border-radius: 50%; background: var(--black); }
  .social li.social-first { background: var(--red); }
</style>
</head>
<body>
<div class="page">
  <div class="backdrop-map" role="img" aria-label="Faint red map of Canada in the background"></div>

  <div class="brand">
    <div class="brand-name">ORV<span class="brand-mark"></span></div>
    <div class="brand-tagline">Your path to study abroad</div>
  </div>

  <div class="headline">
    <div class="headline-top">DARE TO DREAM</div>
    <div class="headline-bottom">CANADIAN...</div>
  </div>

  <ul class="main-nav">
    <li><a href="#"><svg class="nav-arrow" viewBox="0 0 15 12"><path d="M0 4h8V0l7 6-7 6V8H0z" fill="#fff"/></svg>Home</a></li>
    <li class="is-active"><a href="#"><svg class="nav-arrow" viewBox="0 0 15 12"><path d="M0 4h8V0l7 6-7 6V8H0z" fill="#fff"/></svg>About Us</a></li>
    <li><a href="#"><svg class="nav-arrow" viewBox="0 0 15 12"><path d="M0 4h8V0l7 6-7 6V8H0z" fill="#fff"/></svg>Services</a></li>
    <li><a href="#"><svg class="nav-arrow" viewBox="0 0 15 12"><path d="M0 4h8V0l7 6-7 6V8H0z" fill="#fff"/></svg>Contact Us</a></li>
    <li><a href="#"><svg class="nav-arrow" viewBox="0 0 15 12"><path d="M0 4h8V0l7 6-7 6V8H0z" fill="#fff"/></svg>ORV Mission</a></li>
  </ul>

  <main class="content-panel">
    <h1>ABOUT US</h1>
    <p>Delvan Kroth, CEO of Orvane Business Group, has vast knowledge in the field of Student Recruitment &amp; Higher Education. He is an MBA from Canada and is very well known in the India-Canada education corridor since 2004. He has served as India, Africa &amp; Middle East Head for Halvrick College in the past, in addition to providing consultant services for various elite institutions including, Quenmore College, BC, Ostrand Valley College, Ottawa, Tamberlin Technical College, Manitoba, and Varrowfield College, BC.</p>
    <div class="portrait-slot">Image Of<br>Delvan Kroth<br>Comes Here</div>
    <p>Mr. Kroth contributed significantly towards Halvrick College’s immense growth of international students from his region. During his tenure, the college witnessed over <span class="highlight">400% increase</span> in enrolment. This was the highest increase in numbers a medium-sized college in Canada had ever witnessed!</p>
    <p>Mr. Kroth is a seasoned and well-respected professional in the Higher Education sector. His key strengths include Student Recruitment, Counseling and Agent Network Development. Delvan has been a mentor in Training, and Team Lead for successfully launching and establishing overseas education services for various Indian businesses focusing on education. New Service Launches, Market Penetration and Development have been areas of focus for him within the industry.</p>
  </main>

  <div class="member-badge" role="img" aria-label="PLMAT membership badge"></div>
  <p class="copyright">© 2013 orvanegroup.com. All rights reserved.</p>
  <ul class="social" aria-label="Social links">
    <li class="social-first"></li><li></li><li></li><li></li>
  </ul>
</div>
</body>
</html>
```